Home page design for my business

My business will be selling templated drive-in movie theater websites. I would like my business to state to my customers that they get a free website (with hosting fees) where they can take ticket sales digitally. My company will be called Reel-Lanternworks (for Drive In Movie Theatres).

Here are some websites of my potential customers:
https://www.pelorcrest.example/
https://moonglowcinemas.example/
https://oakridgeoutdoorscreen.example/

```html
<!DOCTYPE html>
<html lang="en">
<head>
<meta charset="utf-8">
<title>Reel-Lanternworks — Free Websites for Drive-In Theaters</title>
<link href="https://fonts.googleapis.com/css2?family=Pacifico&family=Delius&display=swap" rel="stylesheet">
<style>
:root{
  --canvas:#ecedef;
  --red:#c8102e;
  --gold:#ae8a2f;
  --white:#ffffff;
  --ink:#1b1b1d;
  --script:"Pacifico", cursive;
  --text:"Delius", sans-serif;
}
*{box-sizing:border-box;margin:0;padding:0}
html,body{width:1153px;height:1200px;overflow:hidden;background:var(--canvas)}
.stage{position:absolute;left:0;top:0;width:1884px;height:1960px;transform:scale(.61199);transform-origin:0 0}

.page{position:absolute;top:96px;width:809px;height:1767px;overflow:hidden;background:var(--page-bg);font-family:var(--text);color:var(--body-ink)}
.page--light{left:91px;--page-bg:#ffffff;--header-bg:#ffffff;--nav-ink:#222;--body-ink:#3a3a3a;--title-ink:#1b1b1d;--accent-ink:var(--red);--band-bg:#f3eee2;--card-ink:#222;--footer-bg:#0e0e10}
.page--dark{left:984px;--page-bg:#101012;--header-bg:#111113;--nav-ink:#f2f2f2;--body-ink:#e6e6e6;--title-ink:#ffffff;--accent-ink:#ffffff;--band-bg:#151518;--card-ink:#f2f2f2;--footer-bg:#141416}

/* header */
.site-header{position:absolute;left:0;top:0;width:809px;height:64px;background:var(--header-bg)}
.brand{position:absolute;display:flex;align-items:center;gap:10px}
.site-header .brand{left:75px;top:8px}
.brand__dot{width:40px;height:40px;border-radius:50%;border:5px solid var(--red)}
.brand__name{font-family:var(--text);font-size:17px;line-height:22px;color:var(--title-ink)}
.nav{position:absolute;left:265px;top:21px;display:flex;font-size:14px;line-height:18px;color:var(--nav-ink)}
.nav span{padding:0 14px;border-left:1px solid rgba(128,128,128,.3)}
.nav span:first-child{border-left:none;color:var(--red)}
.btn{display:inline-flex;align-items:center;justify-content:center;gap:6px;background:var(--red);color:#fff;font-family:var(--text);text-transform:uppercase;border-radius:4px 16px 4px 16px;letter-spacing:.3px;white-space:nowrap}
.login{position:absolute;left:647px;top:14px;width:86px;height:35px;font-size:11px}

/* hero */
.hero{position:absolute;left:0;top:64px;width:809px;height:404px;border-radius:110px 0 110px 0;overflow:hidden;background:linear-gradient(180deg,#2a2d33 0%,#3b3a3a 35%,#1f1e1c 70%,#121212 100%)}
.hero__photo{position:absolute;inset:0;background:radial-gradient(ellipse 260px 110px at 470px 90px,rgba(92,120,140,.55),transparent 70%),radial-gradient(ellipse 200px 90px at 120px 250px,rgba(150,110,60,.35),transparent 70%)}
.hero__title{position:absolute;top:128px;width:100%;text-align:center;font-family:var(--script);font-weight:400;font-size:33px;line-height:44px;color:#fff}
.hero__lead{position:absolute;top:177px;width:100%;text-align:center;font-size:15px;line-height:19px;color:#fff}
.hero .btn{position:absolute;left:352px;top:232px;width:104px;height:34px;font-size:11px}
.chev{position:absolute;width:18px;height:22px}
.hero .chev--prev{left:30px;top:190px}
.hero .chev--next{left:762px;top:190px}
.mouse{position:absolute;left:395px;top:353px}

/* about */
.section-title{position:absolute;width:100%;text-align:center;font-family:var(--script);font-weight:400;font-size:28px;line-height:44px;color:var(--title-ink)}
.section-title em{font-style:normal;color:var(--accent-ink)}
.rule{position:absolute;left:50%;height:2px;background:var(--gold)}
.about-title{top:522px}
.about-rule{top:566px;width:110px;margin-left:-55px}
.copy{position:absolute;left:0;width:100%;text-align:center;font-size:12px;line-height:19px}
.about-copy{top:588px;padding:0 80px}
.about-btn{position:absolute;left:352px;top:669px;width:104px;height:34px;font-size:11px}

/* templates */
.showings{position:absolute;left:0;top:759px;width:809px;height:507px;background:var(--band-bg);border-radius:110px 0 110px 0}
.showings .section-title{top:38px}
.showings .rule{top:88px;width:88px;margin-left:-44px}
.showings .chev--prev{left:30px;top:230px}
.showings .chev--next{left:762px;top:230px}
.card{position:absolute;top:125px;width:208px;text-align:center;color:var(--card-ink)}
.card--1{left:75px}.card--2{left:300px}.card--3{left:526px}
.card__media{position:relative;height:230px;border-radius:18px 0 18px 0;overflow:hidden}
.media--lot{background:linear-gradient(180deg,#2e5b7a 0%,#557a8a 45%,#2a2c2c 75%,#151515 100%)}
.media--couple{background:linear-gradient(180deg,#c9a6a0 0%,#f2dede 40%,#3a2f2e 75%,#181414 100%)}
.media--treat{background:linear-gradient(135deg,#6a6f76 0%,#b7b0a6 45%,#d8c7a2 70%,#a8262b 100%)}
.badge{position:absolute;right:7px;top:7px;width:68px;height:26px;border-radius:3px 10px 3px 10px;background:var(--gold);color:#fff;font-size:11px;line-height:26px}
.card__title{margin-top:13px;font-size:15px;font-weight:400;line-height:20px}
.card__text{margin-top:6px;font-size:10px;line-height:16px;padding:0 6px}
.card .btn{margin-top:10px;width:84px;height:28px;font-size:8.5px}

/* contact */
.contact-frame{position:absolute;left:99px;top:1328px;width:610px;height:136px;border:2px solid var(--gold);border-radius:0 0 14px 0}
.contact-title{position:absolute;top:1305px;left:50%;transform:translateX(-50%);padding:0 14px;background:var(--page-bg);font-family:var(--script);font-weight:400;font-size:27px;line-height:44px;color:var(--title-ink);white-space:nowrap}
.contact-title em{font-style:normal;color:var(--accent-ink)}
.contact-copy{top:1362px;padding:0 130px}
.phone-btn{position:absolute;left:331px;top:1449px;width:148px;height:33px;font-size:11px;text-transform:none;justify-content:flex-end;padding-right:14px;outline:8px solid var(--page-bg)}
.phone-btn__icon{position:absolute;left:4px;top:4px;width:25px;height:25px;border-radius:4px 10px 4px 10px;background:#fff;display:flex;align-items:center;justify-content:center}

/* footer */
.site-footer{position:absolute;left:0;top:1534px;width:809px;height:233px;background:var(--footer-bg);border-radius:110px 0 0 0;color:#fff}
.site-footer .brand{left:318px;top:22px}
.site-footer .brand__name{color:#fff;font-size:18px;line-height:24px}
.foot-rule{position:absolute;left:196px;width:416px;border-top:1px solid #bdbdbd;height:4px;border-bottom:1px solid #bdbdbd}
.foot-rule--top{top:90px}.foot-rule--bottom{top:134px}
.foot-nav{position:absolute;top:108px;width:100%;display:flex;justify-content:center;gap:30px;font-size:12px;line-height:16px;letter-spacing:.4px}
.social{position:absolute;top:162px;width:100%;display:flex;justify-content:center;gap:18px}
.social span{width:12px;height:12px;border-radius:50%;background:#fff}
.foot-line{position:absolute;left:75px;top:196px;width:658px;border-top:1px solid #555}
.legal{position:absolute;top:208px;width:100%;text-align:center;font-size:9.5px;color:#ddd}
</style>
</head>
<body>
<div class="stage">

  <!-- light theme -->
  <div class="page page--light">
    <header class="site-header">
      <div class="brand"><span class="brand__dot"></span><span class="brand__name">Reel-<br>Lanternworks</span></div>
      <nav class="nav"><span>Home</span><span>About</span><span>Templates</span><span>Ticketing</span><span>Contact</span></nav>
      <span class="btn login"><svg width="12" height="12" viewBox="0 0 12 12"><circle cx="6" cy="6" r="5" fill="none" stroke="#fff" stroke-width="1.4"/><circle cx="6" cy="5" r="1.8" fill="#fff"/></svg>Login</span>
    </header>
    <section class="hero">
      <div class="hero__photo" role="img" aria-label="Photo of a drive-in theater at dusk, cars facing a large outdoor screen"></div>
      <h1 class="hero__title">Welcome To Reel-Lanternworks</h1>
      <p class="hero__lead">A free website for your drive-in, hosting included,<br>with digital ticket sales built right in</p>
      <span class="btn">Get Your Site</span>
      <svg class="chev chev--prev" viewBox="0 0 18 22"><path d="M13 3 5 11l8 8" fill="none" stroke="#fff" stroke-width="3"/></svg>
      <svg class="chev chev--next" viewBox="0 0 18 22"><path d="M5 3l8 8-8 8" fill="none" stroke="#fff" stroke-width="3"/></svg>
      <svg class="mouse" width="18" height="34" viewBox="0 0 18 34"><rect x="1" y="1" width="16" height="32" rx="8" fill="none" stroke="#fff" stroke-width="1.6"/><circle cx="9" cy="9" r="1.6" fill="#fff"/><path d="M6 22l3 3 3-3" fill="none" stroke="#fff" stroke-width="1.3"/></svg>
    </section>
    <h2 class="section-title about-title"><em>About</em> Reel-Lanternworks</h2>
    <span class="rule about-rule"></span>
    <p class="copy about-copy">Reel-Lanternworks builds ready-made websites for drive-in movie theaters. Pick a template, add your showtimes and go live for free, with hosting fees covered. Your guests buy tickets online, and you see every sale from one simple dashboard, season after season, with no setup costs.</p>
    <span class="btn about-btn">Get Your Site</span>
    <section class="showings">
      <h2 class="section-title">Featured <em>Templates</em></h2>
      <span class="rule"></span>
      <svg class="chev chev--prev" viewBox="0 0 18 22"><path d="M13 3 5 11l8 8" fill="none" stroke="#1b1b1d" stroke-width="3"/></svg>
      <svg class="chev chev--next" viewBox="0 0 18 22"><path d="M5 3l8 8-8 8" fill="none" stroke="#1b1b1d" stroke-width="3"/></svg>
      <article class="card card--1"><div class="card__media media--lot" role="img" aria-label="Photo of cars parked before a drive-in screen at twilight"><span class="badge">FREE</span></div><h3 class="card__title">Twilight Lot</h3><p class="card__text">Showtimes, car passes and online tickets on one bold home page</p><span class="btn">Preview</span></article>
      <article class="card card--2"><div class="card__media media--couple" role="img" aria-label="Photo of a couple in silhouette watching a bright screen"><span class="badge">FREE</span></div><h3 class="card__title">Date Night</h3><p class="card__text">A warm layout for double features, events and digital ticket sales</p><span class="btn">Preview</span></article>
      <article class="card card--3"><div class="card__media media--treat" role="img" aria-label="Photo of a milkshake and popcorn box on a car tray"><span class="badge">FREE</span></div><h3 class="card__title">Snack Bar</h3><p class="card__text">Sell tickets and concession combos together in a single checkout</p><span class="btn">Preview</span></article>
    </section>
    <div class="contact-frame"></div>
    <h2 class="contact-title"><em>Contact</em> Reel-Lanternworks</h2>
    <p class="copy contact-copy">Ready to sell tickets online? Tell us about your drive-in and we will set up your free template, connect ticket sales and host it for you. Call or write and your new site can be live before your next show.</p>
    <span class="btn phone-btn"><span class="phone-btn__icon"><svg width="13" height="13" viewBox="0 0 24 24"><path d="M6.6 10.8a15 15 0 0 0 6.6 6.6l2.2-2.2a1 1 0 0 1 1-.25 11.4 11.4 0 0 0 3.6.57 1 1 0 0 1 1 1V20a1 1 0 0 1-1 1A17 17 0 0 1 3 4a1 1 0 0 1 1-1h3.5a1 1 0 0 1 1 1c0 1.25.2 2.45.57 3.57a1 1 0 0 1-.25 1z" fill="#c8102e"/></svg></span>+1 (555) 014 2290</span>
    <footer class="site-footer">
      <div class="brand"><span class="brand__dot"></span><span class="brand__name">Reel-<br>Lanternworks</span></div>
      <span class="foot-rule foot-rule--top"></span>
      <nav class="foot-nav"><span>HOME</span><span>ABOUT</span><span>TEMPLATES</span><span>TICKETING</span><span>CONTACT</span></nav>
      <span class="foot-rule foot-rule--bottom"></span>
      <div class="social"><span></span><span></span><span></span><span></span></div>
      <span class="foot-line"></span>
      <p class="legal">© 2022 Reel-Lanternworks &nbsp;|&nbsp; All Rights Reserved</p>
    </footer>
  </div>

  <!-- dark theme -->
  <div class="page page--dark">
    <header class="site-header">
      <div class="brand"><span class="brand__dot"></span><span class="brand__name">Reel-<br>Lanternworks</span></div>
      <nav class="nav"><span>Home</span><span>About</span><span>Templates</span><span>Ticketing</span><span>Contact</span></nav>
      <span class="btn login"><svg width="12" height="12" viewBox="0 0 12 12"><circle cx="6" cy="6" r="5" fill="none" stroke="#fff" stroke-width="1.4"/><circle cx="6" cy="5" r="1.8" fill="#fff"/></svg>Login</span>
    </header>
    <section class="hero">
      <div class="hero__photo" role="img" aria-label="Photo of a drive-in theater at dusk, cars facing a large outdoor screen"></div>
      <h1 class="hero__title">Welcome To Reel-Lanternworks</h1>
      <p class="hero__lead">A free website for your drive-in, hosting included,<br>with digital ticket sales built right in</p>
      <span class="btn">Get Your Site</span>
      <svg class="chev chev--prev" viewBox="0 0 18 22"><path d="M13 3 5 11l8 8" fill="none" stroke="#fff" stroke-width="3"/></svg>
      <svg class="chev chev--next" viewBox="0 0 18 22"><path d="M5 3l8 8-8 8" fill="none" stroke="#fff" stroke-width="3"/></svg>
      <svg class="mouse" width="18" height="34" viewBox="0 0 18 34"><rect x="1" y="1" width="16" height="32" rx="8" fill="none" stroke="#fff" stroke-width="1.6"/><circle cx="9" cy="9" r="1.6" fill="#fff"/><path d="M6 22l3 3 3-3" fill="none" stroke="#fff" stroke-width="1.3"/></svg>
    </section>
    <h2 class="section-title about-title"><em>About</em> Reel-Lanternworks</h2>
    <span class="rule about-rule"></span>
    <p class="copy about-copy">Reel-Lanternworks builds ready-made websites for drive-in movie theaters. Pick a template, add your showtimes and go live for free, with hosting fees covered. Your guests buy tickets online, and you see every sale from one simple dashboard, season after season, with no setup costs.</p>
    <span class="btn about-btn">Get Your Site</span>
    <section class="showings">
      <h2 class="section-title">Featured <em>Templates</em></h2>
      <span class="rule"></span>
      <svg class="chev chev--prev" viewBox="0 0 18 22"><path d="M13 3 5 11l8 8" fill="none" stroke="#fff" stroke-width="3"/></svg>
      <svg class="chev chev--next" viewBox="0 0 18 22"><path d="M5 3l8 8-8 8" fill="none" stroke="#fff" stroke-width="3"/></svg>
      <article class="card card--1"><div class="card__media media--lot" role="img" aria-label="Photo of cars parked before a drive-in screen at twilight"><span class="badge">FREE</span></div><h3 class="card__title">Twilight Lot</h3><p class="card__text">Showtimes, car passes and online tickets on one bold home page</p><span class="btn">Preview</span></article>
      <article class="card card--2"><div class="card__media media--couple" role="img" aria-label="Photo of a couple in silhouette watching a bright screen"><span class="badge">FREE</span></div><h3 class="card__title">Date Night</h3><p class="card__text">A warm layout for double features, events and digital ticket sales</p><span class="btn">Preview</span></article>
      <article class="card card--3"><div class="card__media media--treat" role="img" aria-label="Photo of a milkshake and popcorn box on a car tray"><span class="badge">FREE</span></div><h3 class="card__title">Snack Bar</h3><p class="card__text">Sell tickets and concession combos together in a single checkout</p><span class="btn">Preview</span></article>
    </section>
    <div class="contact-frame"></div>
    <h2 class="contact-title"><em>Contact</em> Reel-Lanternworks</h2>
    <p class="copy contact-copy">Ready to sell tickets online? Tell us about your drive-in and we will set up your free template, connect ticket sales and host it for you. Call or write and your new site can be live before your next show.</p>
    <span class="btn phone-btn"><span class="phone-btn__icon"><svg width="13" height="13" viewBox="0 0 24 24"><path d="M6.6 10.8a15 15 0 0 0 6.6 6.6l2.2-2.2a1 1 0 0 1 1-.25 11.4 11.4 0 0 0 3.6.57 1 1 0 0 1 1 1V20a1 1 0 0 1-1 1A17 17 0 0 1 3 4a1 1 0 0 1 1-1h3.5a1 1 0 0 1 1 1c0 1.25.2 2.45.57 3.57a1 1 0 0 1-.25 1z" fill="#c8102e"/></svg></span>+1 (555) 014 2290</span>
    <footer class="site-footer">
      <div class="brand"><span class="brand__dot"></span><span class="brand__name">Reel-<br>Lanternworks</span></div>
      <span class="foot-rule foot-rule--top"></span>
      <nav class="foot-nav"><span>HOME</span><span>ABOUT</span><span>TEMPLATES</span><span>TICKETING</span><span>CONTACT</span></nav>
      <span class="foot-rule foot-rule--bottom"></span>
      <div class="social"><span></span><span></span><span></span><span></span></div>
      <span class="foot-line"></span>
      <p class="legal">© 2022 Reel-Lanternworks &nbsp;|&nbsp; All Rights Reserved</p>
    </footer>
  </div>

</div>
</body>
</html>
```